A website for Kovadrel Limited

We need a new and modern website for our company. We are engineering consultants and contractors (EPC) in the oil and gas industry and building services industry.
What we do:
Engineering, procurement, construction
Automation (safety and process)
Non-destructive testing
Training
We have an existing website and the content can be referred from there since we are remaking the website
For more information visit Kovadrel Limited Kenya

```html
<!DOCTYPE html>
<html lang="en">
<head>
<meta charset="utf-8">
<title>Kovadrel Limited</title>
<link href="https://fonts.googleapis.com/css2?family=Montserrat:wght@500;600;700;800&family=Open+Sans:wght@400;600;700&display=swap" rel="stylesheet">
<style>
:root{
  --orange:#e8552a;
  --orange-light:#f3894a;
  --orange-pale:#f6a56a;
  --dark:#1d1d1f;
  --darker:#141415;
  --text:#333;
  --muted:#777;
  --grey-bg:#f4f4f4;
  --white:#fff;
}
*{box-sizing:border-box;margin:0;padding:0}
html,body{width:1200px;height:4204px;overflow:hidden}
body{font-family:"Open Sans",Arial,sans-serif;color:var(--text);background:var(--white);position:relative}
h1,h2,h3,.btn,.nav a{font-family:"Montserrat",Arial,sans-serif}
.btn{display:inline-flex;align-items:center;gap:10px;background:var(--orange);color:var(--white);font-weight:700;font-size:15px;padding:0 26px;height:46px;border-radius:23px;text-transform:uppercase;letter-spacing:.5px;box-shadow:0 4px 10px rgba(232,85,42,.3);white-space:nowrap}
.btn .dot{width:18px;height:18px;border-radius:50%;background:var(--white);display:inline-block;position:relative}
.btn .dot::after{content:"";position:absolute;left:6px;top:5px;border-left:7px solid var(--orange);border-top:4px solid transparent;border-bottom:4px solid transparent}
.section-title{font-size:40px;font-weight:700;text-align:center;color:var(--dark);letter-spacing:1px}
.section-title::after{content:"";display:block;width:60px;height:3px;background:var(--orange);margin:12px auto 0}

/* header */
.site-header{position:absolute;top:0;left:0;width:1200px;height:112px;background:var(--white);z-index:5;box-shadow:0 2px 8px rgba(0,0,0,.08)}
.brand{position:absolute;left:96px;top:22px;display:flex;align-items:center;gap:12px}
.brand .mark{width:60px;height:60px;border-radius:50%;background:var(--orange)}
.brand span{font-family:"Montserrat",sans-serif;font-weight:700;font-size:20px;color:var(--orange);line-height:1.1;width:110px}
.topbar{position:absolute;right:80px;top:0;height:40px;display:flex;align-items:center;gap:22px;font-size:13px}
.topbar .pill{background:var(--orange);color:var(--white);padding:0 16px;height:30px;display:flex;align-items:center;gap:8px;border-radius:0 0 8px 8px}
.topbar .social{display:flex;gap:8px}
.topbar .social i{width:16px;height:16px;border-radius:50%;background:var(--orange);display:block}
.nav{position:absolute;left:280px;top:60px;display:flex;gap:20px}
.nav a{font-size:13px;font-weight:600;color:var(--dark);text-decoration:none;text-transform:uppercase;white-space:nowrap}
.nav a.active{color:var(--orange)}
.search{position:absolute;left:896px;top:52px;width:180px;height:34px;border:1px solid #ddd;font-size:13px;color:#999;padding:8px 12px}

/* hero */
.hero{position:absolute;top:112px;left:0;width:1200px;height:710px;overflow:hidden}
.hero .photo{position:absolute;inset:0;background:linear-gradient(180deg,#f5a25a 0%,#e27b3b 30%,#5d6b7a 58%,#1f3a55 78%,#12314e 100%)}
.hero .shade{position:absolute;inset:0;background:linear-gradient(90deg,rgba(0,0,0,.45),rgba(0,0,0,0) 60%)}
.hero-text{position:absolute;left:112px;top:190px;color:var(--white);width:640px}
.hero-text h1{font-size:44px;font-weight:600;line-height:1.1}
.hero-text h1 strong{display:block;font-size:72px;font-weight:700;letter-spacing:2px}
.hero-text p{font-size:17px;font-weight:600;line-height:1.5;margin:18px 0 30px}
.hero svg.curve{position:absolute;bottom:0;left:0}
.down{position:absolute;left:576px;top:776px;width:48px;height:48px;border-radius:50%;background:var(--white);box-shadow:0 2px 8px rgba(0,0,0,.2);z-index:3;display:flex;align-items:center;justify-content:center}

/* what we do */
.what{position:absolute;top:900px;left:0;width:1200px}
.cards{position:absolute;top:100px;left:120px;display:flex;gap:32px}
.service{width:300px;height:480px;background:var(--white);border-radius:10px;box-shadow:0 6px 20px rgba(0,0,0,.12);text-align:center;position:relative}
.service .photo{height:240px;border-radius:10px 10px 0 0}
.service .icon{position:absolute;left:118px;top:196px;width:64px;height:64px;border-radius:50%;background:var(--orange-light);border:4px solid var(--white)}
.service h3{font-size:16px;font-weight:700;margin:40px 0 12px;color:var(--dark)}
.service p{font-size:13px;color:var(--muted);line-height:1.5;padding:0 24px}
.service .btn{margin-top:22px;height:38px;font-size:13px}
.arrow{position:absolute;top:330px;font-size:28px;color:var(--dark)}

/* about */
.about{position:absolute;top:1560px;left:0;width:1200px;height:520px;background:linear-gradient(110deg,var(--orange) 0%,var(--orange-light) 55%,var(--orange-pale) 100%);overflow:hidden}
.about .ring{position:absolute;left:120px;top:60px;width:420px;height:420px;border-radius:50%;border:10px solid var(--white);box-shadow:0 0 0 10px rgba(255,255,255,.3)}
.about .ring .photo{width:100%;height:100%;border-radius:50%;background:linear-gradient(180deg,#f2a35c,#d5652f 55%,#2c3e50)}
.about-text{position:absolute;left:600px;top:120px;width:520px;color:var(--white)}
.about-text h2{font-size:40px;font-weight:700}
.about-text p{font-size:14px;line-height:1.6;margin:16px 0 26px}
.about-text .btn{background:var(--orange);box-shadow:0 4px 12px rgba(0,0,0,.15)}

/* products */
.products{position:absolute;top:2080px;left:0;width:1200px;height:520px;background:var(--grey-bg)}
.products .section-title{padding-top:70px}
.product-row{position:absolute;top:160px;left:112px;display:flex;gap:30px}
.product{width:226px;background:var(--white);box-shadow:0 4px 12px rgba(0,0,0,.08);text-align:center}
.product .photo{height:160px}
.product span{display:block;font-weight:700;font-size:15px;padding:14px 0;color:var(--dark)}
.products .btn{position:absolute;left:510px;top:420px}

/* projects */
.projects{position:absolute;top:2600px;left:0;width:1200px;height:600px}
.projects .section-title{padding-top:84px}
.project-row{position:absolute;top:168px;left:112px;display:flex;gap:24px}
.project-row .photo{width:312px;height:252px}
.projects .btn{position:absolute;left:510px;top:468px}

/* contact */
.contact{position:absolute;top:3200px;left:0;width:1200px;height:640px;background:linear-gradient(120deg,var(--orange),var(--orange-light))}
.contact h2{color:var(--white);text-align:center;font-size:40px;font-weight:700;padding-top:72px}
.form{position:absolute;left:192px;top:160px;width:816px;height:190px}
.field{position:absolute;left:0;width:388px;height:54px;border-radius:27px;background:var(--white);font-size:14px;color:#999;padding:17px 24px}
.field.msg{left:416px;top:0;width:400px;height:186px;border-radius:20px}
.contact .btn{position:absolute;left:500px;top:400px;background:transparent;border:2px solid var(--white);box-shadow:none}

/* footer */
.footer{position:absolute;top:3780px;left:0;width:1200px;height:380px;background:var(--dark);color:#ccc}
.footer svg{position:absolute;top:-60px;left:0}
.foot-brand{position:absolute;left:112px;top:70px;display:flex;align-items:center;gap:14px}
.foot-brand .mark{width:80px;height:80px;border-radius:50%;background:var(--orange)}
.foot-brand span{font-family:"Montserrat",sans-serif;font-weight:700;font-size:24px;color:var(--orange);width:140px;line-height:1.1}
.col{position:absolute;top:60px}
.col h3{font-size:16px;color:var(--white);font-weight:700;margin-bottom:18px}
.col li{list-style:none;font-size:13px;line-height:26px}
.contact-list li{display:flex;gap:10px;align-items:flex-start;margin-bottom:12px;line-height:20px}
.contact-list i{flex:0 0 22px;height:22px;border-radius:50%;background:#3a3a3c;display:block}
.sub p{font-size:13px;line-height:1.5;width:300px}
.sub .box{margin-top:18px;width:300px;height:38px;background:var(--white);border-radius:4px;position:relative;font-size:12px;color:#999;padding:11px 12px}
.sub .box b{position:absolute;right:0;top:0;width:40px;height:38px;background:var(--orange);border-radius:0 4px 4px 0}
.sub .soc{display:flex;gap:10px;margin-top:18px}
.sub .soc i{width:30px;height:30px;border-radius:50%;background:var(--white);display:block}
.bottom{position:absolute;top:4160px;left:0;width:1200px;height:44px;background:var(--darker);color:#bbb;font-size:13px;display:flex;align-items:center;justify-content:space-between;padding:0 112px}
.bottom b{color:var(--orange)}
.chat{position:absolute;right:24px;top:4100px;width:44px;height:44px;border-radius:50%;background:var(--orange)}
</style>
</head>
<body>

<header class="site-header">
  <div class="brand"><div class="mark"></div><span>Kovadrel Limited</span></div>
  <div class="topbar">
    <span>&#9742; +254 700 410 226</span>
    <span class="pill">&#9993; info@kovadrel.co.ke</span>
    <span class="social"><i></i><i></i><i></i></span>
  </div>
  <nav class="nav">
    <a class="active">Home</a><a>About Us</a><a>Services</a><a>What We Do</a><a>Products</a><a>Projects</a><a>Contact Us</a>
  </nav>
  <div class="search">Search</div>
</header>

<section class="hero">
  <div class="photo" role="img" aria-label="Offshore oil platform and supply vessel at sunset"></div>
  <div class="shade"></div>
  <div class="hero-text">
    <h1>WELCOME TO<strong>KOVADREL</strong></h1>
    <p>Kovadrel undertakes Design, Supply, Installation and Commissioning of LPG and Petroleum Systems including LPG Reticulated Systems.</p>
    <span class="btn">Get Started <i class="dot"></i></span>
  </div>
  <svg class="curve" width="1200" height="120" viewBox="0 0 1200 120"><path d="M0 120 L0 70 Q600 -40 1200 70 L1200 120Z" fill="#e8552a" opacity=".9"/><path d="M0 120 L0 92 Q600 0 1200 92 L1200 120Z" fill="#fff"/></svg>
</section>
<div class="down"><svg width="18" height="18" viewBox="0 0 18 18"><path d="M3 4l6 5 6-5M3 9l6 5 6-5" stroke="#e8552a" stroke-width="2" fill="none"/></svg></div>

<section class="what">
  <h2 class="section-title">WHAT WE DO</h2>
  <span class="arrow" style="left:44px">&#8249;</span>
  <span class="arrow" style="left:1140px">&#8250;</span>
  <div class="cards">
    <article class="service">
      <div class="photo" role="img" aria-label="Engineers inspecting an industrial site" style="background:linear-gradient(160deg,#8fa6bb,#42566a)"></div>
      <div class="icon"></div>
      <h3>Engineering, procurement,construction</h3>
      <p>Lorem ipsum dolor sit amet consectetur adipiscing elit sed do eiusmod tempor incididunt ut labore et dolore magna..</p>
      <span class="btn">Read More</span>
    </article>
    <article class="service">
      <div class="photo" role="img" aria-label="Technician working at an automation control panel" style="background:linear-gradient(160deg,#5b8fb5,#1f3c57)"></div>
      <div class="icon"></div>
      <h3>Automation</h3>
      <p>Lorem ipsum dolor sit amet consectetur adipiscing elit sed do eiusmod tempor incididunt ut labore et dolore magna..</p>
      <span class="btn">Read More</span>
    </article>
    <article class="service">
      <div class="photo" role="img" aria-label="Trainees in a workshop session" style="background:linear-gradient(160deg,#c9b59a,#6a5a48)"></div>
      <div class="icon"></div>
      <h3>Training</h3>
      <p>Lorem ipsum dolor sit amet consectetur adipiscing elit sed do eiusmod tempor incididunt ut labore et dolore magna..</p>
      <span class="btn">Read More</span>
    </article>
  </div>
</section>

<section class="about">
  <div class="ring"><div class="photo" role="img" aria-label="Offshore drilling rig at dusk"></div></div>
  <div class="about-text">
    <h2>ABOUT US</h2>
    <p>Kovadrel undertakes Design, Supply, Installation and Commissioning of LPG and Petroleum Systems including LPG Reticulated Systems, gland gas and fire suppression works. We serve oil companies, multinationals and local firms, government agencies, manufacturing companies, agricultural institutions and the building services industry.</p>
    <span class="btn">Read More <i class="dot"></i></span>
  </div>
</section>

<section class="products">
  <h2 class="section-title">OUR PRODUCTS</h2>
  <div class="product-row">
    <div class="product"><div class="photo" role="img" aria-label="Industrial pipework and valves" style="background:linear-gradient(150deg,#e0a04a,#6b4a2e)"></div><span>EPC</span></div>
    <div class="product"><div class="photo" role="img" aria-label="Offshore petroleum platform" style="background:linear-gradient(180deg,#a9c4d9,#2e5674)"></div><span>Petroleum</span></div>
    <div class="product"><div class="photo" role="img" aria-label="Engineer with automation equipment" style="background:linear-gradient(150deg,#3d5a80,#141d2b)"></div><span>Automation</span></div>
    <div class="product"><div class="photo" role="img" aria-label="Red fire fighting pipe system" style="background:linear-gradient(150deg,#e04a3a,#7a1e1a)"></div><span>Fire Fighting</span></div>
  </div>
  <span class="btn">View More <i class="dot"></i></span>
</section>

<section class="projects">
  <h2 class="section-title">OUR PROJECTS</h2>
  <div class="project-row">
    <div class="photo" role="img" aria-label="Plant pipework with red valves" style="background:linear-gradient(150deg,#d9d9d9,#8a2f2a)"></div>
    <div class="photo" role="img" aria-label="Colourful process pipes in a plant room" style="background:linear-gradient(150deg,#c65a30,#273a57)"></div>
    <div class="photo" role="img" aria-label="Refinery towers under blue sky" style="background:linear-gradient(180deg,#8db7d8,#6c7a80)"></div>
  </div>
  <span class="btn">View More <i class="dot"></i></span>
</section>

<section class="contact">
  <h2>CONTACT US</h2>
  <div class="form">
    <div class="field" style="top:0">Name</div>
    <div class="field" style="top:66px">Email Address</div>
    <div class="field" style="top:132px">Phone Number</div>
    <div class="field msg">Message</div>
  </div>
  <span class="btn">Submit Now <i class="dot"></i></span>
</section>

<footer class="footer">
  <svg width="1200" height="61" viewBox="0 0 1200 61"><path d="M0 61 L0 40 Q600 -30 1200 40 L1200 61Z" fill="#1d1d1f"/></svg>
  <div class="foot-brand"><div class="mark"></div><span>Kovadrel Limited</span></div>
  <div class="col" style="left:400px">
    <h3>QUICK LINKS</h3>
    <ul><li>Home</li><li>About Us</li><li>Services</li><li>What we do</li><li>Products</li><li>Projects</li><li>Contact Us</li></ul>
  </div>
  <div class="col contact-list" style="left:592px">
    <h3>CONTACT US</h3>
    <ul>
      <li><i></i>+254 700 410 226</li>
      <li><i></i>info@kovadrel.co.ke</li>
      <li><i></i>Nyali Plaza, Suite 7,<br>Ngong Road</li>
      <li><i></i>0207 555 010</li>
    </ul>
  </div>
  <div class="col sub" style="left:832px">
    <h3>SUBSCRIBE TO OUR BLOG</h3>
    <p>Sign up today to get resources on how to attract and retain more customers!</p>
    <div class="box">Email Address<b></b></div>
    <div class="soc"><i></i><i></i><i></i></div>
  </div>
</footer>
<div class="bottom">
  <span>Copyright&copy; 2023 <b>Kovadrel</b> | All Rights Reserved</span>
  <span>Specifications &nbsp;|&nbsp; Site Map &nbsp;|&nbsp; Privacy Policy</span>
</div>
<div class="chat"></div>

</body>
</html>
```